Business Card Design

We need a business card designed for our new company. Prefer a black card with white logo & writing.

Contact Information for Business Card

Ted Galloway, address: 7-4812 Fernhollow Road, Abbotsford, BC, V3K 8R2, Office Phone: 604-712-3390, Cell: 604-947-2164, Email: ted@resinworkshub.ca

Colors

Designer to choose only greyscale colors for use in the design.

```html
<!DOCTYPE html>
<html lang="en">
<head>
<meta charset="utf-8">
<title>Resinworks Hub — Business Card</title>
<link rel="stylesheet" href="https://fonts.googleapis.com/css2?family=Poppins:wght@300;400;600;800&display=swap">
<style>
  :root {
    --stage: #2a2a2b;
    --card: #2b2c2e;
    --card-back: #222325;
    --rim: #cfcfcf;
    --ink: #ffffff;
    --ink-soft: #d9d9d9;
    --band-ink: #1e1e1e;
    --divider: #9a9a9a;
  }
  * { margin: 0; padding: 0; box-sizing: border-box; }
  html, body {
    width: 1200px; height: 711px; overflow: hidden;
    background: var(--stage);
    font-family: "Poppins", sans-serif;
  }
  .sheet {
    position: relative; width: 1200px; height: 711px;
    display: flex; align-items: center; justify-content: center; gap: 40px;
  }
  .card {
    position: relative; width: 540px; height: 310px;
    border-radius: 22px; overflow: hidden;
    box-shadow: 0 0 0 2px var(--rim), 0 14px 30px rgba(0,0,0,.55);
  }
  /* back */
  .card-back { background: var(--card-back); }
  .back-pattern {
    position: absolute; inset: 0;
    background: linear-gradient(135deg, #303133 0%, #1f2022 55%, #262729 100%);
  }
  /* front */
  .card-front { background: var(--card); color: var(--ink); }
  .brand {
    position: absolute; left: 0; top: 72px; width: 215px;
    display: flex; flex-direction: column; align-items: center;
  }
  .brand-mark {
    width: 24px; height: 24px; background: var(--ink); margin-bottom: 10px;
  }
  .brand-name {
    font-weight: 800; font-size: 25px; line-height: 1.1;
    text-align: center; letter-spacing: 1px; color: var(--ink);
  }
  .divider {
    position: absolute; left: 222px; top: 30px; width: 1px; height: 200px;
    background: var(--divider);
  }
  .contact { position: absolute; left: 252px; top: 42px; }
  .person-name { font-size: 32px; line-height: 1; font-weight: 300; white-space: nowrap; }
  .person-name .first { font-weight: 800; }
  .person-role { font-size: 15px; font-weight: 400; color: var(--ink-soft); margin-top: 4px; }
  .contact-list { list-style: none; margin-top: 18px; }
  .contact-list li {
    display: flex; align-items: center; gap: 10px; white-space: nowrap;
    font-size: 14.5px; font-weight: 300; height: 24px; color: var(--ink-soft);
  }
  .contact-list svg { width: 14px; height: 14px; fill: var(--ink); flex: none; }
  .address-band {
    position: absolute; left: 0; bottom: 30px; width: 460px; height: 32px;
    background: var(--ink); color: var(--band-ink);
    clip-path: polygon(0 0, 100% 0, 94% 50%, 100% 100%, 0 100%);
    display: flex; align-items: center; padding-left: 34px;
    font-size: 14.5px; font-weight: 400; white-space: nowrap;
  }
  .layers-ornament {
    position: absolute; right: 16px; bottom: 26px; width: 66px; height: 46px;
    background: linear-gradient(160deg, #ffffff 0%, #9a9a9a 55%, #5e5e5e 100%);
    clip-path: polygon(20% 10%, 100% 0, 85% 45%, 70% 100%, 0 90%);
  }
</style>
</head>
<body>
<main class="sheet">
  <section class="card card-back" aria-label="Card back">
    <div class="back-pattern" role="img" aria-label="Repeating pattern of the company name in subtle gloss tones on black"></div>
  </section>

  <section class="card card-front" aria-label="Card front">
    <div class="brand">
      <span class="brand-mark"></span>
      <span class="brand-name">RESINWORKS<br>HUB</span>
    </div>
    <span class="divider"></span>
    <div class="contact">
      <h1 class="person-name"><span class="first">Ted</span> Galloway</h1>
      <p class="person-role">Founder &amp; CEO</p>
      <ul class="contact-list">
        <li><svg viewBox="0 0 24 24"><path d="M6.6 10.8a15.1 15.1 0 0 0 6.6 6.6l2.2-2.2a1 1 0 0 1 1-.25 11.4 11.4 0 0 0 3.6.57 1 1 0 0 1 1 1V20a1 1 0 0 1-1 1A17 17 0 0 1 3 4a1 1 0 0 1 1-1h3.5a1 1 0 0 1 1 1c0 1.25.2 2.45.57 3.57a1 1 0 0 1-.25 1z"/></svg>604-712-3390</li>
        <li><svg viewBox="0 0 24 24"><path d="M7 1h10a2 2 0 0 1 2 2v18a2 2 0 0 1-2 2H7a2 2 0 0 1-2-2V3a2 2 0 0 1 2-2zm0 3v14h10V4zm5 15.5a1.2 1.2 0 1 0 0 2.4 1.2 1.2 0 0 0 0-2.4z"/></svg>604-947-2164</li>
        <li><svg viewBox="0 0 24 24"><path d="M12 2a10 10 0 1 0 0 20 10 10 0 0 0 0-20zm6.9 6h-3a15.6 15.6 0 0 0-1.4-3.6A8 8 0 0 1 18.9 8zM12 4c.8 1.2 1.5 2.5 1.9 4h-3.8c.4-1.5 1.1-2.8 1.9-4zM4.3 14a8 8 0 0 1 0-4h3.4a16 16 0 0 0 0 4zm.8 2h3a15.6 15.6 0 0 0 1.4 3.6A8 8 0 0 1 5.1 16zm3-8h-3a8 8 0 0 1 4.4-3.6A15.6 15.6 0 0 0 8.1 8zM12 20c-.8-1.2-1.5-2.5-1.900-4h3.8c-.4 1.5-1.1 2.8-1.9 4zm2.3-6H9.7a14.7 14.7 0 0 1 0-4h4.6a14.7 14.7 0 0 1 0 4zm.2 5.6a15.6 15.6 0 0 0 1.4-3.6h3a8 8 0 0 1-4.4 3.6zm1.8-5.6a16 16 0 0 0 0-4h3.4a8 8 0 0 1 0 4z"/></svg>www.resinworkshub.ca</li>
        <li><svg viewBox="0 0 24 24"><path d="M3 5h18a1 1 0 0 1 1 1v12a1 1 0 0 1-1 1H3a1 1 0 0 1-1-1V6a1 1 0 0 1 1-1zm1 2.4V17h16V7.4l-8 5.3zM5.6 7 12 11.2 18.4 7z"/></svg>ted@resinworkshub.ca</li>
      </ul>
    </div>
    <div class="layers-ornament" role="img" aria-label="Stacked floor-coating layers graphic in white and greys"></div>
    <p class="address-band">7-4812 Fernhollow Road, Abbotsford, BC, V3K 8R2.</p>
  </section>
</main>
</body>
</html>
```